Bellwyn Rockcraft- Business Card Design

We need a business card design for a new company based in Canberra ACT. We build Rock Retaining Walls, commercial and domestic.
We would like to see designs that use BR letters combine as logo and use stone sandstone or blue rocks. Final design of the business card should communicate strong, wealthy, Rock retaining walls

Target Market(s)

Everybody who needs stone retaining wall in there backyard

Industry/Entity Type

Business

Contact Information for Business Card

BR
Bellwyn Rockcraft,
Tavo Marlek (Stonemason)
Phone/ 0438 917 264
PO Box 3958 Denholm ACT 2917
E-mail/tmarlek@fernpost.net.au
www.bellwynrockcraft.com.au

Requirements
Must have
• Letters BR combine as logo. "BELLWYN ROCKCRAFT" as features
Nice to have
• Rock: Sandstone or bluestone

```html
<!DOCTYPE html>
<html lang="en">
<head>
<meta charset="utf-8">
<title>Bellwyn Rockcraft – Business Card</title>
<link rel="stylesheet" href="https://fonts.googleapis.com/css2?family=Oswald:wght@600&family=Jost:wght@600;700&family=Arimo&display=swap">
<style>
  :root {
    --page: #ffffff;
    --slate: #61656e;
    --slate-text: #5f636b;
    --bluestone: #939db4;
    --pale-stone: #eff0f3;
    --dark-stone: #6f7480;
    --white: #ffffff;
    --rule: #8a8d94;
  }
  * { margin: 0; padding: 0; box-sizing: border-box; }
  html, body { width: 1200px; height: 1200px; overflow: hidden; background: var(--page); }
  .sheet { position: relative; width: 1200px; height: 1200px; }
  .side-label {
    position: absolute; left: 187px;
    font-family: "Arimo", Arial, sans-serif; font-size: 14px; color: #222;
  }
  .card { position: absolute; left: 187px; width: 807px; height: 466px; overflow: hidden; }
  .card--front { top: 114px; border: 1px solid var(--rule); background: var(--white); }
  .card--back { top: 650px; background: var(--slate); }
  .stone-band { position: absolute; left: 0; right: 0; bottom: 0; height: 76px; }
  .card--front .stone-band { background: var(--pale-stone); }
  .card--back .stone-band { background: var(--dark-stone); height: 80px; }

  .brand-mark {
    position: absolute; left: 342px; top: 62px; width: 124px; height: 124px;
    background: var(--slate-text); border-radius: 6px;
  }
  .brand-name {
    position: absolute; left: 0; right: 0; text-align: center;
    font-family: "Oswald", "Arial Narrow", sans-serif; font-weight: 600;
    color: var(--slate-text); line-height: 1;
  }
  .brand-name__top { top: 254px; font-size: 28px; letter-spacing: 22px; padding-left: 22px; }
  .brand-name__main { top: 284px; font-size: 62px; letter-spacing: 0.5px; }

  .back-circle {
    position: absolute; left: 308px; top: 44px; width: 190px; height: 190px;
    border-radius: 50%; background: var(--dark-stone); opacity: 0.7;
  }
  .person { position: absolute; left: 0; right: 0; text-align: center; line-height: 1; }
  .person__name {
    top: 118px; font-family: "Oswald", "Arial Narrow", sans-serif; font-weight: 600;
    font-size: 50px; color: var(--white);
  }
  .person__role {
    top: 176px; font-family: "Jost", sans-serif; font-weight: 700;
    font-size: 15px; letter-spacing: 17px; padding-left: 17px; color: var(--bluestone);
  }
  .contact {
    position: absolute; left: 0; right: 0; text-align: center;
    font-family: "Jost", sans-serif; font-weight: 700; color: var(--white);
    letter-spacing: 3px; line-height: 1;
  }
  .contact__row { top: 280px; font-size: 19px; }
  .contact__label { color: var(--bluestone); font-size: 14px; letter-spacing: 0.5px; margin-right: 6px; }
  .contact__gap { display: inline-block; width: 28px; }
  .contact__address { top: 330px; font-size: 19px; }
  .contact__web { top: 359px; font-size: 18px; letter-spacing: 2.6px; }
</style>
</head>
<body>
<div class="sheet">
  <div class="side-label" style="top:90px">FRONT</div>
  <section class="card card--front">
    <div class="brand-mark"></div>
    <div class="brand-name brand-name__top">BELLWYN</div>
    <div class="brand-name brand-name__main">ROCKCRAFT</div>
    <div class="stone-band" role="img" aria-label="Pale stacked stone wall pattern along the lower edge"></div>
  </section>

  <div class="side-label" style="top:626px">BACK</div>
  <section class="card card--back">
    <div class="back-circle"></div>
    <div class="person person__name">TAVO MARLEK</div>
    <div class="person person__role">STONEMASON</div>
    <div class="contact contact__row">
      <span class="contact__label">PHONE:</span>0438 917 264<span class="contact__gap"></span><span class="contact__label">EMAIL:</span>tmarlek@fernpost.net.au
    </div>
    <div class="contact contact__address">PO Box 3958 Denholm ACT 2917</div>
    <div class="contact contact__web">www.bellwynrockcraft.com.au</div>
    <div class="stone-band" role="img" aria-label="Dark stacked stone wall pattern along the lower edge"></div>
  </section>
</div>
</body>
</html>
```